Letterhead Design Project

Please do not submit designs until I upload file-

Project Deadline Extended

Requirements
Must have
• clean lines and font- easy to read; consistent with the design on the business card
Does not use too much of the real estate of the size of the paper

```html
<!DOCTYPE html>
<html lang="en">
<head>
<meta charset="utf-8">
<title>The Summit Ridge Foundation – Letterhead</title>
<link href="https://fonts.googleapis.com/css2?family=Questrial&display=swap" rel="stylesheet">
<style>
  :root {
    --backdrop: #e6e7e8;
    --paper: #f8f8f8;
    --navy: #1f3f6e;
    --slate: #6c7375;
    --ink: #3a3f42;
  }
  html, body {
    margin: 0;
    padding: 0;
    width: 1200px;
    height: 795px;
    overflow: hidden;
    background: var(--backdrop);
  }
  .letterhead {
    position: absolute;
    left: 306px;
    top: 17px;
    width: 587px;
    height: 760px;
    background: var(--paper);
    box-shadow: 0 2px 10px rgba(0,0,0,0.12);
    font-family: "Questrial", sans-serif;
    color: var(--ink);
  }
  .edge-band {
    position: absolute;
    left: 0;
    width: 12px;
  }
  .edge-band--navy {
    top: 0;
    height: 596px;
    background: var(--navy);
  }
  .edge-band--slate {
    top: 606px;
    bottom: 0;
    width: 14px;
    background: var(--slate);
  }
  .brand {
    position: absolute;
    left: 44px;
    top: 58px;
    display: flex;
    align-items: center;
    gap: 8px;
  }
  .brand-square {
    width: 22px;
    height: 22px;
    background: var(--navy);
  }
  .brand-name {
    margin: 0;
    font-size: 10.5px;
    line-height: 1.05;
    letter-spacing: 0.04em;
    text-transform: uppercase;
    color: var(--navy);
    font-weight: 400;
  }
  .contact {
    position: absolute;
    left: 56px;
    bottom: 36px;
    margin: 0;
    font-style: normal;
    font-size: 8.5px;
    line-height: 14px;
    letter-spacing: 0.06em;
  }
  .contact-line {
    display: flex;
    align-items: center;
    gap: 8px;
  }
  .contact-icon {
    width: 8px;
    height: 8px;
    flex: none;
    fill: none;
    stroke: var(--navy);
    stroke-width: 1.2;
  }
</style>
</head>
<body>
  <main class="letterhead">
    <div class="edge-band edge-band--navy"></div>
    <div class="edge-band edge-band--slate"></div>

    <header class="brand">
      <span class="brand-square"></span>
      <p class="brand-name">The<br>Summit Ridge<br>Foundation</p>
    </header>

    <address class="contact">
      <div class="contact-line">4810 Harbor Crest Avenue, Suite 305</div>
      <div class="contact-line">Palm Harbor, FL 34683</div>
      <div class="contact-line">
        <svg class="contact-icon" viewBox="0 0 8 8"><rect x="1.5" y="0.6" width="5" height="6.8" rx="0.8"/></svg>
        +1-727-555-0148
      </div>
      <div class="contact-line">
        <svg class="contact-icon" viewBox="0 0 8 8"><rect x="0.6" y="1.5" width="6.8" height="5"/><polyline points="0.6,1.5 4,4.4 7.4,1.5"/></svg>
        dana.wells@summitridgefoundation.org
      </div>
      <div class="contact-line">
        <svg class="contact-icon" viewBox="0 0 8 8"><circle cx="4" cy="4" r="3.3"/><line x1="0.7" y1="4" x2="7.3" y2="4"/><ellipse cx="4" cy="4" rx="1.4" ry="3.3"/></svg>
        www.summitridgefoundation.org
      </div>
    </address>
  </main>
</body>
</html>
```